jQuery Mobile CSS for web app

Task Outline:
Create jQuery Mobile themeroller compliant CSS and icons for a mobile web app.
Task Description:
Brindle Solutions are in the process of implementing a new, web based version of their Tessel operations platform.
The web based version of Tessel is built on top of the jQuery Mobile platform and we are looking for a designer to create a jQuery Mobile themeroller compliant CSS theme pack that we can plug into our application. The aim is to remove the standard jQuery Mobile look and feel and to introduce the Brindle branding throughout the new web app.
A number of screenshots are shown in the attached design spec (brindle_solutions.pdf) that show what the current (Windows Mobile 6.5) application looks like, alongside the development version of our new web app.
Deliverables:
• jQuery Mobile (v 1.4.2) themeroller compliant CSS which provides theming for all jQuery Mobile UI components.
• Example html showing how to use the CSS theme (especially where additional html/css classes are required).
• New set of status icons (as listed in attachment)
Inspiration:
See our website for current branding: www.brindle-solutions-demo.net

```html
<!DOCTYPE html>
<html lang="en">
<head>
<meta charset="utf-8">
<title>Brindle – Item Search</title>
<link href="https://fonts.googleapis.com/css2?family=Open+Sans:wght@400;600&display=swap" rel="stylesheet">
<style>
  :root{
    --bg:#1b1b1b;
    --header-top:#2e2e2e;
    --header-bottom:#1e1e1e;
    --divider:#3a3a3a;
    --label:#a9a9a9;
    --text:#ffffff;
    --muted:#c4c4c4;
    --input-bg:#ffffff;
    --input-text:#7a7a7a;
    --seg-active-top:#5a5a5a;
    --seg-active-bottom:#3c3c3c;
    --seg-idle-top:#2a2a2a;
    --seg-idle-bottom:#000000;
    --red-top:#d22a33;
    --red-bottom:#a8151e;
    --row-top:#5b5b5b;
    --row-bottom:#323232;
    --footer-active:#c8c8c8;
    --footer-idle-top:#2c2c2c;
    --footer-idle-bottom:#171717;
    --icon-grey:#8a8a8a;
  }
  *{box-sizing:border-box;margin:0;padding:0}
  html,body{width:830px;height:1200px;overflow:hidden;background:var(--bg)}
  body{font-family:"Open Sans",Arial,sans-serif;color:var(--text);position:relative}

  .app-header{position:absolute;left:0;top:0;width:830px;height:122px;
    background:linear-gradient(var(--header-top),var(--header-bottom));border-bottom:1px solid #111}
  .brand-name{position:absolute;left:39px;top:30px;font-size:50px;font-weight:400;line-height:1;color:var(--text)}
  .header-divider{position:absolute;top:18px;width:1px;height:86px;background:var(--divider)}
  .launchpad{position:absolute;left:307px;top:28px;width:248px;height:65px;border-radius:5px;
    background:linear-gradient(#8a8a8a,#6a6a6a);display:flex;align-items:center;padding-left:16px;
    font-size:18px;color:var(--text)}
  .launchpad svg{margin-right:18px}
  .menu-toggle{position:absolute;left:762px;top:44px}

  .field-label{position:absolute;left:53px;top:164px;font-size:24px;color:var(--label)}
  .search-input{position:absolute;left:51px;top:223px;width:731px;height:70px;border-radius:5px;
    background:var(--input-bg);font-size:22px;color:var(--input-text);padding:18px 0 0 27px}

  .segmented{position:absolute;left:51px;top:325px;width:731px;height:67px;display:flex;
    border:1px solid #444;border-radius:4px;overflow:hidden}
  .segment{flex:1;display:flex;align-items:center;justify-content:center;font-size:20px;
    background:linear-gradient(var(--seg-idle-top),var(--seg-idle-bottom));border-left:1px solid #4a4a4a}
  .segment:first-child{border-left:none}
  .segment.is-active{background:linear-gradient(var(--seg-active-top),var(--seg-active-bottom))}

  .btn-search{position:absolute;left:566px;top:423px;width:215px;height:72px;border-radius:4px;
    background:linear-gradient(var(--red-top),var(--red-bottom));display:flex;align-items:center;
    justify-content:center;font-size:25px;color:var(--text)}
  .btn-search svg{margin-right:18px}

  .section-rule{position:absolute;left:0;top:538px;width:830px;height:2px;background:#262626}
  .section-title{position:absolute;left:51px;top:558px;font-size:25px;color:var(--label)}

  .result-list{position:absolute;left:51px;top:629px;width:724px;list-style:none}
  .result-item{height:136px;border-top:1px solid #6a6a6a;border-bottom:1px solid #1a1a1a;
    background:linear-gradient(var(--row-top),var(--row-bottom));position:relative}
  .result-icon{position:absolute;left:32px;top:27px}
  .result-title{position:absolute;left:139px;top:28px;font-size:31px;line-height:1}
  .result-sub{position:absolute;left:139px;top:76px;font-size:21px;color:var(--muted)}

  .app-footer{position:absolute;left:0;top:1083px;width:830px;height:117px;display:flex}
  .footer-btn{flex:1;display:flex;align-items:center;justify-content:center;
    background:linear-gradient(var(--footer-idle-top),var(--footer-idle-bottom));border-left:1px solid #3a3a3a;position:relative}
  .footer-btn.is-active{background:var(--footer-active);border-left:none}
  .footer-code{position:absolute;right:28px;top:46px;font-size:17px;color:var(--text)}
</style>
</head>
<body>
  <header class="app-header">
    <div class="brand-name">Brindle</div>
    <span class="header-divider" style="left:277px"></span>
    <div class="launchpad">
      <svg width="34" height="34" viewBox="0 0 34 34" aria-hidden="true">
        <g fill="#d8d8d8">
          <rect x="1" y="1" width="5" height="5"/><rect x="10" y="1" width="5" height="5"/><rect x="19" y="1" width="5" height="5"/><rect x="28" y="1" width="5" height="5"/>
          <rect x="1" y="10" width="5" height="5"/><rect x="10" y="10" width="5" height="5"/><rect x="19" y="10" width="5" height="5"/><rect x="28" y="10" width="5" height="5"/>
          <rect x="1" y="19" width="5" height="5"/><rect x="10" y="19" width="5" height="5"/><rect x="19" y="19" width="5" height="5"/><rect x="28" y="19" width="5" height="5"/>
          <rect x="1" y="28" width="5" height="5"/><rect x="10" y="28" width="5" height="5"/><rect x="19" y="28" width="5" height="5"/><rect x="28" y="28" width="5" height="5"/>
        </g>
      </svg>
      LAUNCHPAD
    </div>
    <span class="header-divider" style="left:729px"></span>
    <svg class="menu-toggle" width="36" height="32" viewBox="0 0 36 32" aria-label="Menu">
      <g fill="#ffffff"><rect y="0" width="36" height="4"/><rect y="14" width="36" height="4"/><rect y="28" width="36" height="4"/></g>
    </svg>
  </header>

  <div class="field-label">Customer Name</div>
  <div class="search-input">Cable</div>

  <div class="segmented">
    <div class="segment is-active">Serail Number</div>
    <div class="segment">Item number</div>
    <div class="segment">Description</div>
  </div>

  <div class="btn-search">
    <svg width="30" height="30" viewBox="0 0 30 30" aria-hidden="true">
      <circle cx="12" cy="12" r="9" fill="none" stroke="#f3c9cb" stroke-width="3"/>
      <line x1="19" y1="19" x2="27" y2="27" stroke="#f3c9cb" stroke-width="3.5" stroke-linecap="round"/>
    </svg>
    Search
  </div>

  <div class="section-rule"></div>
  <div class="section-title">Results</div>

  <ul class="result-list">
    <li class="result-item">
      <svg class="result-icon" width="82" height="82" viewBox="0 0 82 82" aria-hidden="true">
        <circle cx="41" cy="41" r="39" fill="#3b3b3b" stroke="#7a7a7a" stroke-width="3"/>
        <circle cx="41" cy="41" r="30" fill="#555"/>
        <path d="M41 24 L56 32 L56 50 L41 58 L26 50 L26 32 Z" fill="var(--icon-grey)"/>
        <path d="M26 32 L41 40 L56 32 M41 40 L41 58" fill="none" stroke="#555" stroke-width="2.5"/>
      </svg>
      <div class="result-title">30106</div>
      <div class="result-sub">RAD64002142; L 62 ca...</div>
    </li>
    <li class="result-item">
      <svg class="result-icon" width="82" height="82" viewBox="0 0 82 82" aria-hidden="true">
        <circle cx="41" cy="41" r="39" fill="#3b3b3b" stroke="#7a7a7a" stroke-width="3"/>
        <circle cx="41" cy="41" r="30" fill="#555"/>
        <path d="M41 24 L56 32 L56 50 L41 58 L26 50 L26 32 Z" fill="var(--icon-grey)"/>
        <path d="M26 32 L41 40 L56 32 M41 40 L41 58" fill="none" stroke="#555" stroke-width="2.5"/>
      </svg>
      <div class="result-title">30106</div>
      <div class="result-sub">RAD64002142; L 62 ca...</div>
    </li>
    <li class="result-item">
      <svg class="result-icon" width="82" height="82" viewBox="0 0 82 82" aria-hidden="true">
        <circle cx="41" cy="41" r="39" fill="#3b3b3b" stroke="#7a7a7a" stroke-width="3"/>
        <circle cx="41" cy="41" r="30" fill="#555"/>
        <path d="M41 24 L56 32 L56 50 L41 58 L26 50 L26 32 Z" fill="var(--icon-grey)"/>
        <path d="M26 32 L41 40 L56 32 M41 40 L41 58" fill="none" stroke="#555" stroke-width="2.5"/>
      </svg>
      <div class="result-title">30106</div>
      <div class="result-sub">RAD64002142; L 62 ca...</div>
    </li>
  </ul>

  <footer class="app-footer">
    <div class="footer-btn is-active">
      <svg width="70" height="46" viewBox="0 0 70 46" aria-label="Back">
        <path d="M22 6 L6 16 L22 26" fill="none" stroke="#111" stroke-width="5" stroke-linejoin="round"/>
        <path d="M8 16 H50 A13 13 0 0 1 50 42 H18" fill="none" stroke="#111" stroke-width="5"/>
      </svg>
    </div>
    <div class="footer-btn">
      <svg width="80" height="42" viewBox="0 0 80 42" aria-label="Home">
        <path d="M3 40 V18 L40 3 L77 18 V40 Z" fill="none" stroke="#8a8a8a" stroke-width="3.5" stroke-linejoin="round"/>
      </svg>
    </div>
    <div class="footer-btn">
      <svg width="70" height="46" viewBox="0 0 70 46" aria-label="Forward">
        <path d="M48 6 L64 16 L48 26" fill="none" stroke="#8a8a8a" stroke-width="5" stroke-linejoin="round"/>
        <path d="M62 16 H20 A13 13 0 0 0 20 42 H52" fill="none" stroke="#8a8a8a" stroke-width="5"/>
      </svg>
      <span class="footer-code">C8</span>
    </div>
  </footer>
</body>
</html>
```